Plakat-Design 24h Betreuung
Zielgruppe
Wir vermitteln 24h Pflege- und Betreuungskräfte für alte und hilfbedürftige Menschen!
Zielgruppe: deren Angehörige (zwischen 50-70 Jahre alt)
Aufgabenstellung
Klare Ansage - nicht zu verspielt - geradlinig
Maße Plakat: 504 cm breit x 238 cm hoch
Das PLAKAT ist ca 10 m von der Straße entfernet und ist für Autofahrer gedacht - somit muss man alles gut lesen können und groß geschrieben sein !!!!
Folgender Text und Bilder sollte das Plakat beinhalten:
24h - Betreuung (groß links oben platziert)
Logo: SorgeFreund.at
Foto mit 10 Personen
Erfahrung seit 2010
www.sorgefreund.at

```html
<!DOCTYPE html>
<html lang="de">
<head>
<meta charset="utf-8">
<title>24h-Betreuung – SorgeFreund.at</title>
<link rel="stylesheet" href="https://fonts.googleapis.com/css2?family=Montserrat:wght@600;700;800&display=swap">
<style>
  :root {
    --backdrop: #e0e0df;
    --paper: #ffffff;
    --navy: #2b4081;
    --orange: #d7691e;
    --photo-light: #f2f3f6;
    --photo-mid: #c9cfdf;
  }
  * { margin: 0; padding: 0; box-sizing: border-box; }
  html, body {
    width: 1200px;
    height: 704px;
    overflow: hidden;
    background: var(--backdrop);
    font-family: "Montserrat", Arial, sans-serif;
  }
  .poster {
    position: absolute;
    left: 71px;
    top: 71px;
    width: 1058px;
    height: 562px;
    background: var(--paper);
    overflow: hidden;
  }
  .headline {
    position: absolute;
    left: 0;
    right: 0;
    top: 26px;
    text-align: center;
    color: var(--navy);
    font-weight: 800;
    font-size: 80px;
    line-height: 1;
    letter-spacing: 1px;
  }
  .team-photo {
    position: absolute;
    left: 278px;
    top: 136px;
    width: 537px;
    height: 395px;
    border-radius: 40px 40px 20px 20px;
    background: radial-gradient(ellipse at 50% 45%, var(--photo-mid) 0%, var(--photo-light) 70%, var(--paper) 100%);
  }
  .base-band {
    position: absolute;
    left: 0;
    right: 0;
    bottom: 0;
    height: 15px;
    background: var(--navy);
  }
  .experience-badge {
    position: absolute;
    left: 0;
    top: 0;
    width: 1058px;
    height: 562px;
  }
  .experience-text {
    position: absolute;
    left: 0;
    top: 407px;
    width: 254px;
    text-align: center;
    color: var(--paper);
    font-weight: 600;
    font-size: 38px;
    line-height: 41px;
  }
  .brand-name {
    position: absolute;
    left: 700px;
    top: 480px;
    width: 300px;
    text-align: center;
    color: var(--navy);
    font-weight: 700;
    font-size: 38px;
    line-height: 1;
  }
</style>
</head>
<body>
  <main class="poster">
    <h1 class="headline">24h - Betreuung</h1>

    <div class="team-photo" role="img" aria-label="Gruppenfoto des Teams: zehn Personen, überwiegend in weißen Blusen mit dunkelblauen Tüchern und Jeans, in der Mitte eine Frau im blauen Kostüm und ein Mann im dunklen Sakko"></div>

    <svg class="experience-badge" viewBox="0 0 1058 562" aria-hidden="true">
      <circle cx="123" cy="477" r="148" fill="var(--orange)"/>
      <circle cx="123" cy="477" r="135" fill="var(--navy)"/>
    </svg>

    <div class="base-band"></div>

    <p class="experience-text">Erfahrung<br>seit<br>2010</p>

    <p class="brand-name">SorgeFreund.at</p>
  </main>
</body>
</html>
```